Poster Design Project for Over 50's Gym

We need a poster design to advertise our over 50's gym. We want to attract older adults who love enjoying their age, living life and having a bit of fun.
We would like to see a bright, fun, non-intimidating poster communicating how easy exercise can be and how great it can be for your health.
I would like the poster to include the following information.
Title:
Mackay's Over 50's Gym
Exercise with confidence
How old would you be if you didn't know your age?
Suitable exercise programmes for all medical conditions
Friendly and non-intimidating environment
Private health insurance rebates
University qualified exercise physiologists
Bright Pines Exercise Physiology Clinic
Exercise Physiologists Dorothy Linwell & Tobias Brandt
Suite 7, 238 Ridgeview Road, Mackay
www.tallowbrookfit.com.au
MON - FRI 8:30 am - 6:30 pm
I have photos available for use & Logo just unable to attach at moment****
Over 50 adult
Medical

```html
<!DOCTYPE html>
<html lang="en">
<head>
<meta charset="utf-8">
<title>Mackay's Over 50's Gym</title>
<link rel="stylesheet" href="https://fonts.googleapis.com/css2?family=PT+Sans:wght@400;700&family=Roboto+Condensed:wght@700&display=swap">
<style>
  :root {
    --navy: #233b7a;
    --navy-deep: #1c3068;
    --orange: #f26a1f;
    --yellow: #fbb92f;
    --gold-title: #fbb534;
    --white: #ffffff;
    --sticker: #cdd0d4;
    --ink: #111111;
    --bullet: #3f8ee0;
  }
  * { margin: 0; padding: 0; box-sizing: border-box; }
  html, body { width: 900px; height: 1200px; overflow: hidden; background: var(--white); }
  .poster {
    position: relative; width: 900px; height: 1200px; overflow: hidden;
    font-family: "PT Sans", Arial, sans-serif;
  }
  .backdrop { position: absolute; inset: 0; width: 900px; height: 1200px; }
  .brand {
    position: absolute; left: 240px; top: 48px;
    display: flex; align-items: center; gap: 16px;
  }
  .brand-dot { width: 70px; height: 70px; border-radius: 50%; background: var(--orange); }
  .brand-name {
    color: var(--navy); font-weight: 700; font-size: 44px; line-height: 1;
  }
  .brand-name span { display: block; font-size: 33px; margin-top: 4px; }
  .contact-line {
    position: absolute; left: 326px; color: var(--ink);
    font-size: 20px;
  }
  .contact-line.address { top: 162px; }
  .contact-line.web { top: 190px; color: var(--navy); font-weight: 700; letter-spacing: 1px; }
  .headline {
    position: absolute; top: 295px; left: 0; width: 900px; text-align: center;
    font-family: "Roboto Condensed", "Arial Narrow", sans-serif;
    font-size: 68px; color: var(--gold-title); letter-spacing: 1px;
  }
  .question {
    position: absolute; left: 66px; top: 420px; width: 420px;
    color: var(--white); font-weight: 700; font-size: 27px; line-height: 1.4;
  }
  .benefits { position: absolute; left: 66px; top: 528px; width: 500px; list-style: none; }
  .benefits li {
    display: flex; align-items: center; gap: 12px;
    color: var(--white); font-size: 17px; height: 29px; white-space: nowrap;
  }
  .benefits li::before {
    content: ""; flex: none; width: 19px; height: 19px; border-radius: 50%;
    background: radial-gradient(circle at 35% 30%, #cfe6ff 0%, var(--bullet) 55%, #1b5aa6 100%);
    border: 2px solid #9cb3d8;
  }
  .hours {
    position: absolute; left: 590px; top: 455px; width: 280px; text-align: center;
    color: var(--white);
  }
  .hours-days { font-size: 48px; color: #e8ecf6; }
  .hours-times { font-size: 39px; font-weight: 700; line-height: 1.1; margin-top: 6px; }
  .sticker {
    position: absolute; left: 98px; top: 665px; width: 250px; height: 250px;
    border-radius: 50%; background: var(--sticker);
    box-shadow: 4px 6px 12px rgba(0,0,0,0.35);
    display: flex; align-items: center; justify-content: center; text-align: center;
    color: var(--navy); font-weight: 700; font-size: 34px; line-height: 1.2;
  }
  .sticker::after {
    content: ""; position: absolute; right: 6px; top: 14px; width: 50px; height: 50px;
    background: linear-gradient(225deg, var(--white) 0%, #e7e9ec 50%, #9aa0a8 100%);
    border-radius: 0 0 0 40px;
  }
  .call {
    position: absolute; left: 95px; top: 925px; font-size: 28px; color: var(--ink);
  }
  .call strong { font-size: 38px; font-weight: 700; margin-left: 6px; }
  .team {
    position: absolute; left: 57px; top: 985px; width: 342px; height: 188px;
    background: var(--navy); border-radius: 10px; padding: 10px 12px;
  }
  .team-title { color: var(--gold-title); font-weight: 700; font-size: 22px; text-align: center; }
  .team-grid { display: flex; justify-content: space-between; margin-top: 4px; }
  .member { width: 154px; text-align: center; }
  .member-name { color: var(--white); font-size: 13px; margin-bottom: 4px; }
  .member-photo {
    width: 154px; height: 112px; border: 3px solid var(--white);
    background: linear-gradient(160deg, #c9c5bd 0%, #8b8c93 55%, #3d4a6e 100%);
  }
</style>
</head>
<body>
<div class="poster">
  <svg class="backdrop" viewBox="0 0 900 1200" preserveAspectRatio="none" aria-hidden="true">
    <defs>
      <linearGradient id="heartFill" x1="0" y1="0" x2="1" y2="1">
        <stop offset="0" stop-color="#2b2d33"/>
        <stop offset="0.45" stop-color="#d9d2c6"/>
        <stop offset="1" stop-color="#f1efe9"/>
      </linearGradient>
    </defs>
    <rect width="900" height="1200" fill="var(--yellow)"/>
    <path d="M0,205 C260,290 560,300 900,255 L900,900 C700,860 420,840 0,700 Z" fill="var(--navy)"/>
    <path d="M0,0 H900 V240 C600,262 300,250 0,190 Z" fill="var(--white)"/>
    <path d="M0,190 C300,250 600,262 900,240 L900,256 C560,282 260,268 0,206 Z" fill="var(--orange)"/>
    <path d="M0,178 C280,235 600,250 900,232 L900,242 C600,260 300,248 0,190 Z" fill="var(--yellow)"/>
    <path d="M0,700 C300,800 560,850 760,860 L760,880 C540,870 280,830 0,740 Z" fill="var(--orange)"/>
    <path d="M0,740 C280,830 540,870 760,880 L760,895 C520,885 260,850 0,770 Z" fill="var(--yellow)"/>
    <path d="M706,775 C650,680 520,660 452,725 C390,790 410,905 505,1010 L585,1200 L900,1200 L900,705 C830,668 748,690 706,775 Z" fill="var(--orange)"/>
    <path d="M706,790 C655,702 530,686 470,740 C414,795 432,900 520,1000 L600,1200 L900,1200 L900,725 C830,690 752,708 706,790 Z" fill="var(--white)"/>
    <path role="img" aria-label="Photo of a smiling older woman in a white polo shirt in the gym" d="M706,808 C660,725 540,708 486,756 C436,805 452,900 536,992 L616,1200 L900,1200 L900,745 C830,712 756,728 706,808 Z" fill="url(#heartFill)"/>
  </svg>

  <div class="brand">
    <div class="brand-dot"></div>
    <div class="brand-name">Bright Pines<span>Exercise Physiology Clinic</span></div>
  </div>
  <p class="contact-line address">Suite 7, 238 Ridgeview Road Mackay Q 4740</p>
  <p class="contact-line web">www.tallowbrookfit.com.au</p>

  <h1 class="headline">Mackay's Over 50's Gym</h1>

  <p class="question">How old would you be<br>if you didn't know your age?</p>
  <ul class="benefits">
    <li>Suitable exercise programmes for all medical conditions</li>
    <li>Friendly and non-intimidating environment</li>
    <li>Private health insurance rebates</li>
    <li>University qualified exercise physiologists</li>
  </ul>

  <div class="hours">
    <div class="hours-days">MON - FRI</div>
    <div class="hours-times">8:30 am to<br>6:30 pm</div>
  </div>

  <div class="sticker">EXERCISE<br>WITH<br>CONFIDENCE</div>

  <p class="call">Call Us: <strong>4821 3064</strong></p>

  <section class="team">
    <h2 class="team-title">EXERCISE PHYSIOLOGISTS</h2>
    <div class="team-grid">
      <div class="member">
        <p class="member-name">Dorothy Linwell</p>
        <div class="member-photo" role="img" aria-label="Photo of exercise physiologist Dorothy Linwell in the gym"></div>
      </div>
      <div class="member">
        <p class="member-name">Tobias Brandt</p>
        <div class="member-photo" role="img" aria-label="Photo of exercise physiologist Tobias Brandt in the gym"></div>
      </div>
    </div>
  </section>
</div>
</body>
</html>
```